CONTACT US Page and design for website

We need a contact us page for our website. We would like it to have a message area, a map, our information, etc.

Please see the text attachment for what we are looking for. We need to have something that is creative and interesting, modern and professional.

We believe that a contact US page should be very creative because everyone clicks that to contact us. We want it to be super professional, attention grabbing, pleasing to the eye.

PLEASE KEEP THE HEADER AND FOOTER THE SAME, ONLY THE ACTUAL CONTACT US PAGE NEEDS TO BE WORKED ON. THANKS!
We are excited to work with designers for this project.

Target Market(s)

Clients in technology business

Industry/Entity Type

Information Technology

Number of Pages Required

1 page

Font styles to use
Serif

Requirements
Must have
• CHECK THE TEXT ATTACHMENT PLEASE
• Must stay within our design colors and theme.
Nice to have
• see attachment
Should not have
• it should be special

```html
<!DOCTYPE html>
<html lang="en">
<head>
<meta charset="utf-8">
<title>Contact Us – Novacore Tech</title>
<link href="https://fonts.googleapis.com/css2?family=Open+Sans:wght@400;600;700&family=Lobster&display=swap" rel="stylesheet">
<style>
:root{
  --teal:#2ba8a2;
  --teal-dark:#23918c;
  --ink:#333;
  --muted:#666;
  --line:#e3e3e3;
  --card:#f7f7f7;
  --grey-head:#a9a9ad;
  --footer:#a5a5a5;
  --footer-bottom:#999;
  --white:#fff;
}
*{box-sizing:border-box;margin:0;padding:0}
html,body{width:806px;height:1200px;overflow:hidden}
body{position:relative;background:var(--white);font-family:"Open Sans",Arial,sans-serif;color:var(--ink)}
.abs{position:absolute}

/* header */
.account-pill{left:614px;top:0;width:124px;height:22px;background:#a8a8ad;border-radius:0 0 14px 14px;display:flex;font-size:8px;color:#333;align-items:center}
.account-pill span{flex:1;text-align:center}
.account-pill span+span{border-left:1px solid #8f8f94}
.brand{left:66px;top:24px;display:flex;align-items:center;gap:10px}
.brand-dot{width:38px;height:38px;border-radius:50%;background:var(--teal)}
.brand-name{font-size:22px;font-weight:600;color:var(--teal);letter-spacing:2px;line-height:1}
.brand-tag{font-size:6px;letter-spacing:3px;color:var(--teal);margin-top:3px}
.header-contact{top:38px;display:flex;align-items:center;gap:10px;font-size:8.5px}
.ring{width:28px;height:28px;border-radius:50%;border:1px solid #ccc;display:flex;align-items:center;justify-content:center;box-shadow:0 1px 3px rgba(0,0,0,.12)}
.header-line{left:0;top:74px;width:806px;height:1px;background:var(--line)}
.nav{left:66px;top:90px;display:flex;gap:17px;font-size:8px;color:#444}
.search{left:623px;top:85px;width:79px;height:22px;border:1px solid #bbb;border-radius:11px;font-size:7px;color:#666;padding:6px 11px}
.search svg{position:absolute;right:10px;top:6px}
.cart{left:714px;top:84px;width:25px;height:25px;border-radius:50%;border:1px solid #999;display:flex;align-items:center;justify-content:center}
.nav-line{left:0;top:116px;width:806px;height:1px;background:var(--line)}
.crumb{left:0;top:117px;width:806px;height:30px;background:var(--teal);border-bottom:2px solid var(--teal-dark);font-size:8.5px;color:var(--white);padding:9px 66px}
.crumb b{font-weight:400;color:#e9f7f6}
.crumb em{font-style:normal;color:#123}

/* cards */
.card{top:179px;width:155px;height:110px;background:var(--card);border:1px solid #eee;box-shadow:0 1px 3px rgba(0,0,0,.06);padding:26px 0 0 30px;font-size:8px}
.card h3{font-size:10px;font-weight:600;color:var(--teal);margin-bottom:9px;letter-spacing:.3px}
.card p{display:flex;align-items:center;gap:10px;margin-bottom:10px;color:#333}
.card.social{padding-left:19px;padding-top:28px}
.card.social h3{font-size:11px}
.socials{display:flex;gap:4px}
.socials i{width:26px;height:26px;border-radius:50%;display:block}

/* map */
.map{left:66px;top:324px;width:674px;height:256px;background:linear-gradient(135deg,#dcdcdc,#cfd3d4 60%,#d6dad0)}
.map-pin{left:424px;top:432px}
.pin-label{left:435px;top:451px;font-size:6px;font-weight:700;color:#9b1c1c}
.office{left:351px;top:462px;width:156px;height:87px;background:var(--white);box-shadow:0 1px 4px rgba(0,0,0,.2);padding:16px 0 0 16px;font-size:7.5px;line-height:14.5px}
.office h4{font-size:7.5px;font-weight:600}

/* form */
.form-title{left:66px;top:615px;font-size:12.5px;font-weight:500;letter-spacing:.4px}
.field{left:66px;width:285px;border:1px solid #eee;border-radius:3px;font-size:7.5px;color:#777;padding:12px 15px;box-shadow:0 1px 2px rgba(0,0,0,.04)}
.submit{left:66px;top:876px;width:79px;height:32px;background:var(--teal);border-radius:3px;color:var(--white);font-size:9px;font-weight:700;display:flex;align-items:center;justify-content:center;box-shadow:0 2px 0 var(--teal-dark)}
.form-dot{left:393px;top:750px;width:24px;height:24px;border-radius:50%;background:var(--teal)}

/* hours */
.hours{left:460px;top:642px;width:280px;height:259px;background:var(--teal);border:1px solid var(--teal-dark)}
.hours svg.head{position:absolute;left:0;top:0}
.hours h2{position:absolute;top:20px;width:100%;text-align:center;color:var(--white);font-size:13px;font-weight:600;letter-spacing:.5px}
.hours .lead{position:absolute;top:82px;width:100%;text-align:center;font-family:"Lobster",cursive;color:var(--white);font-size:11.5px;line-height:17px}
.hours ul{position:absolute;left:73px;top:123px;list-style:none;color:var(--white);font-size:8.5px}
.hours li{display:flex;align-items:center;gap:9px;height:26px}

/* footer */
.footer{left:0;top:946px;width:806px;height:216px;background:var(--footer);color:var(--white)}
.footer h5{position:absolute;top:42px;font-size:11px;font-weight:700;letter-spacing:.4px}
.about{position:absolute;left:67px;top:70px;width:194px;font-size:7.5px;line-height:14.4px;text-align:justify}
.fcontact{position:absolute;left:309px;top:70px;font-size:7.5px;line-height:12px}
.fcontact div{display:flex;gap:9px;margin-bottom:11px}
.frings{display:flex;gap:3px}
.frings i{width:22px;height:22px;border:1px solid var(--white);border-radius:50%;display:block}
.links{position:absolute;top:71px;list-style:none;font-size:7.5px}
.links li{height:21.3px;display:flex;gap:12px}
.bottom{left:0;top:1162px;width:806px;height:38px;background:var(--footer-bottom);color:var(--white);font-size:7.5px;text-align:center;padding-top:14px}
</style>
</head>
<body>

<header>
  <div class="abs account-pill"><span>SIGN UP</span><span>LOG IN</span></div>
  <div class="abs brand">
    <span class="brand-dot"></span>
    <div><div class="brand-name">NOVACORE</div><div class="brand-tag">BUILT FOR WHAT'S NEXT</div></div>
  </div>
  <div class="abs header-contact" style="left:546px">
    <span class="ring"><svg width="11" height="10" viewBox="0 0 11 10"><path d="M1 1h9v6H5L2 9V7H1z" fill="#555"/></svg></span>LIVE CHAT
  </div>
  <div class="abs header-contact" style="left:641px;font-size:10px">
    <span class="ring"><svg width="11" height="11" viewBox="0 0 11 11"><path d="M2 1l2 0 1 3-1.3 1a6 6 0 002.3 2.3L7 6l3 1v2c0 .6-.5 1-1 1C5 10 1 6 1 2c0-.5.4-1 1-1z" fill="var(--teal)"/></svg></span>555-014-2200
  </div>
  <div class="abs header-line"></div>
  <nav class="abs nav"><span>SERVERS</span><span>WORKSTATIONS</span><span>COMPONENTS</span><span>VIRTUAL REALITY</span><span>DRONES</span><span>ABOUT US</span><span>BLOG</span><span>RESOURCES</span><span>CONTACT US</span></nav>
  <div class="abs search">Search<svg width="8" height="8" viewBox="0 0 8 8"><circle cx="3.3" cy="3.3" r="2.4" fill="none" stroke="var(--teal)" stroke-width="1.2"/><path d="M5 5l2.5 2.5" stroke="var(--teal)" stroke-width="1.3"/></svg></div>
  <div class="abs cart"><svg width="11" height="9" viewBox="0 0 11 9"><path d="M1 3h9l-1 5H2z" fill="var(--teal)"/><path d="M3 3l2-2M8 3L6 1" stroke="var(--teal)"/></svg></div>
  <div class="abs nav-line"></div>
  <div class="abs crumb"><b>HOME</b> <em>/</em> CONTACT US</div>
</header>

<main>
  <section class="abs card" style="left:66px">
    <h3>GENERAL INQUIRIES</h3>
    <p><svg width="7" height="10" viewBox="0 0 7 10"><rect x=".6" y=".6" width="5.8" height="8.8" rx="1" fill="none" stroke="#333" stroke-width="1.1"/></svg>(555)014-2200</p>
    <p><svg width="11" height="8" viewBox="0 0 11 8"><rect x=".5" y=".5" width="10" height="7" fill="none" stroke="#333"/><path d="M.5 .5l5 4 5-4" fill="none" stroke="#333"/></svg>info@novacoretech.com</p>
  </section>
  <section class="abs card" style="left:238px">
    <h3>SALES INQUIRIES</h3>
    <p><svg width="7" height="10" viewBox="0 0 7 10"><rect x=".6" y=".6" width="5.8" height="8.8" rx="1" fill="none" stroke="#333" stroke-width="1.1"/></svg>(555)014-2200</p>
    <p><svg width="11" height="8" viewBox="0 0 11 8"><rect x=".5" y=".5" width="10" height="7" fill="none" stroke="#333"/><path d="M.5 .5l5 4 5-4" fill="none" stroke="#333"/></svg>sales@novacoretech.com</p>
  </section>
  <section class="abs card" style="left:412px;padding-left:19px">
    <h3>PURCHASING INQUIRIES</h3>
    <p><svg width="7" height="10" viewBox="0 0 7 10"><rect x=".6" y=".6" width="5.8" height="8.8" rx="1" fill="none" stroke="#333" stroke-width="1.1"/></svg>(555)014-2201</p>
    <p><svg width="11" height="8" viewBox="0 0 11 8"><rect x=".5" y=".5" width="10" height="7" fill="none" stroke="#333"/><path d="M.5 .5l5 4 5-4" fill="none" stroke="#333"/></svg>purchasing@novacoretech.com</p>
  </section>
  <section class="abs card social" style="left:585px">
    <h3>STAY CONNECTED</h3>
    <div class="socials"><i style="background:#3b5998"></i><i style="background:#dd4b39"></i><i style="background:#0e76a8"></i><i style="background:#8a5a44"></i></div>
  </section>

  <div class="abs map" role="img" aria-label="Street map of the neighbourhood around the office headquarters"></div>
  <svg class="abs map-pin" width="12" height="20" viewBox="0 0 12 20"><path d="M6 0a6 6 0 016 6c0 4-6 14-6 14S0 10 0 6a6 6 0 016-6z" fill="#d33"/><circle cx="6" cy="6" r="2" fill="#8b1010"/></svg>
  <div class="abs pin-label">4120 Marlow Avenue</div>
  <div class="abs office">
    <h4>OFFICE HEADQUARTERS</h4>
    Novacore Tech, LLC.<br>4120 Marlow Ave.<br>Westbrook, CA 91390
  </div>

  <h2 class="abs form-title">CONTACT FORM</h2>
  <div class="abs field" style="top:652px;height:33px">Name</div>
  <div class="abs field" style="top:693px;height:32px">E-mail</div>
  <div class="abs field" style="top:733px;height:32px">Phone Number</div>
  <div class="abs field" style="top:773px;height:93px">Message</div>
  <div class="abs submit">SUBMIT</div>
  <div class="abs form-dot"></div>

  <section class="abs hours">
    <svg class="head" width="278" height="66" viewBox="0 0 278 66"><path d="M0 0h278v37L139 66 0 37z" fill="var(--grey-head)"/></svg>
    <h2>HOURS OF OPERATION</h2>
    <p class="lead">Our dedicated customer service representatives<br>are available 24/7 by phone.</p>
    <ul>
      <li><svg width="8" height="8" viewBox="0 0 8 8"><rect y="1" width="8" height="7" fill="#fff"/><rect x="1" y="3" width="6" height="4" fill="var(--teal)"/></svg>Monday: 8:00am- 5:00pm</li>
      <li><svg width="8" height="8" viewBox="0 0 8 8"><rect y="1" width="8" height="7" fill="#fff"/><rect x="1" y="3" width="6" height="4" fill="var(--teal)"/></svg>Tuesday: 8:00am- 5:00pm</li>
      <li><svg width="8" height="8" viewBox="0 0 8 8"><rect y="1" width="8" height="7" fill="#fff"/><rect x="1" y="3" width="6" height="4" fill="var(--teal)"/></svg>Wednesday: 8:00am- 5:00pm</li>
      <li><svg width="8" height="8" viewBox="0 0 8 8"><rect y="1" width="8" height="7" fill="#fff"/><rect x="1" y="3" width="6" height="4" fill="var(--teal)"/></svg>Thursday: 8:00am- 5:00pm</li>
      <li><svg width="8" height="8" viewBox="0 0 8 8"><rect y="1" width="8" height="7" fill="#fff"/><rect x="1" y="3" width="6" height="4" fill="var(--teal)"/></svg>Friday: 8:00am- 5:00pm</li>
    </ul>
  </section>
</main>

<footer>
  <div class="abs footer">
    <h5 style="left:67px">ABOUT US</h5>
    <p class="about">Based in Westbrook California, Novacore Tech offers custom servers, storage, and workstations for local businesses in Los Angeles, Beverly Hills, Thousand Oaks, Ventura, Orange County, Santa Barbara, Oxnard, Irvine, Anaheim, and San Diego. Novacore Tech also offers such products to clients throughout the United States and Worldwide.</p>

    <h5 style="left:309px">CONTACT US</h5>
    <div class="fcontact">
      <div><svg width="10" height="9" viewBox="0 0 10 9"><path d="M5 0l5 4H8.5v5h-2.5V6H4v3H1.5V4H0z" fill="#fff"/></svg><span>4120 Marlow Ave.Westbrook,<br>CA 91390</span></div>
      <div><svg width="10" height="10" viewBox="0 0 7 10"><rect x=".6" y=".6" width="5.8" height="8.8" rx="1" fill="none" stroke="#fff" stroke-width="1.1"/></svg><span>Call Us :&nbsp; (555)014-2200</span></div>
      <div><svg width="11" height="8" viewBox="0 0 11 8"><rect x=".5" y=".5" width="10" height="7" fill="none" stroke="#fff"/><path d="M.5 .5l5 4 5-4" fill="none" stroke="#fff"/></svg><span>Mail Us :&nbsp; sales@novacoretech.com</span></div>
      <div class="frings"><i></i><i></i><i></i><i></i></div>
    </div>

    <h5 style="left:491px">QUICK LINKS</h5>
    <ul class="links" style="left:491px">
      <li><span>»</span>Computer Hardware</li><li><span>»</span>Drones</li><li><span>»</span>Virtual Reality</li><li><span>»</span>About Us</li><li><span>»</span>Customer Support</li>
    </ul>

    <h5 style="left:638px">OTHER LINKS</h5>
    <ul class="links" style="left:638px">
      <li><span>»</span>Terms and Conditions</li><li><span>»</span>Warranty Information</li><li><span>»</span>Contact Us</li><li><span>»</span>Return Policy</li>
    </ul>
  </div>
  <div class="abs bottom">@copyright 2017 Novacore Tech.All Rights Reserved</div>
</footer>

</body>
</html>
```